Tarvolen - Tarvolen Border Flow Reshaping Trade

Web Design for international start-up, which is automating customs clearance processes for forwarding companies by applying a web application, which is operating with artificial intelligence and robotic process automation. Tarvolen pursues the vision of supporting forwarding companies successfully in becoming digital masters and co-creates innovative software solutions with all participants (ex- and importers of goods) along value-added chains. With intelligent/smart/digital customs clearance software or in other words, a virtual customs clearance roboter tailord to the customers needs, we are transforming businesses. The website could look like this:

https://www.plomix.com/uk-en/index.php
or
https://sitebrenna.com/theme/halvering

Please use colours and designs you think would be the best fit. These websites are just here to give you an idea of how the webdesign could look like. Use the attached logo design as a basis for further web design. You can use the provided pictures, but you can also use your own ones, if you think they are better suited. But please take care, that they have a high resolution quality.

Description of Website: The website is transparent and modern. It provides seven pages such as homepage, products, web app, the about us, working at Tarvolen, News, contact us and search results page. The homepage or landing page should be filled with a short description of the company, what Tarvolen is doing, how they will support its customers and will also include a video of the provided solution. Products provide obviously information about different products and their characteristics. Web app page includes information about principles and technologies that get the software going. The about us page includes unique advantages and value propositions for customers and the contact us, as the name already says, will provide contact information and possibilities to contact us. The rest is also obvious (for additional information look up the website of PLX, priorly provided link - the page is also available in english).

If you have any questions, I am happy to answer them any time.
Updates

I have to think about the text that I want to have included into the design and hadn't have the time to compose it.

Target Market(s)

Forwarding Companies, Ex-/Importers

Industry/Entity Type

It Company

Number of Pages Required

5+ page

Requirements
Must have
• The web design should be designes according to the attached logo of Tarvolen.

```html
<!DOCTYPE html>
<html lang="en">
<head>
<meta charset="utf-8">
<title>Tarvolen – Tarvolen Border Flow</title>
<link rel="stylesheet" href="https://fonts.googleapis.com/css2?family=Orbitron:wght@700;800&family=Roboto:wght@400;500;700&display=swap">
<style>
  :root{
    --brand-blue:#2f4a9e;
    --brand-cyan:#1cb2d6;
    --accent-orange:#f47420;
    --ink:#1d1d1d;
    --muted:#5a5a5a;
    --page-bg:#eef0f3;
    --footer-bg:#1c2a3b;
    --circle-dark:#1f3f7e;
    --white:#ffffff;
  }
  *{box-sizing:border-box;margin:0;padding:0}
  html,body{width:1200px;height:3021px;overflow:hidden}
  body{font-family:"Roboto",Arial,sans-serif;background:var(--page-bg);color:var(--ink)}
  .page{position:relative;width:1200px;height:3021px;overflow:hidden}
  .backdrop{position:absolute;inset:0}
  .abs{position:absolute}

  /* header */
  .site-header{position:absolute;top:0;left:0;width:1200px;height:107px;background:var(--white);border-top:4px solid var(--brand-cyan);z-index:3}
  .brand{position:absolute;left:143px;top:22px;display:flex;align-items:center;gap:10px}
  .brand-square{width:22px;height:22px;background:var(--brand-cyan)}
  .brand-name{font-family:"Roboto",sans-serif;font-weight:700;font-size:40px;color:var(--brand-blue);line-height:1}
  .brand-tag{position:absolute;left:175px;top:66px;font-size:12px;color:#555}
  .main-nav{position:absolute;left:408px;top:46px;display:flex;gap:15px;font-size:14px;font-weight:500;color:#111;letter-spacing:.1px}
  .nav-search{position:absolute;left:1042px;top:47px}

  /* hero */
  .hero-title{position:absolute;top:278px;left:0;width:1200px;text-align:center;font-weight:500;font-size:86px;color:var(--white);line-height:1}
  .hero-tag{position:absolute;top:360px;left:581px;font-size:20px;color:#fff}
  .hero-lede{position:absolute;top:408px;left:0;width:1200px;text-align:center;font-size:21px;line-height:31px;color:#fff}
  .btn{position:absolute;display:flex;align-items:center;justify-content:center;gap:10px;background:var(--accent-orange);color:#fff;font-weight:500;font-size:19px;border-radius:27px;height:53px}
  .btn-arrow{width:16px;height:16px;border-radius:50%;background:#fff;position:relative}
  .btn-arrow::after{content:"";position:absolute;left:4px;top:4px;border-left:7px solid var(--accent-orange);border-top:4px solid transparent;border-bottom:4px solid transparent}
  .hero-dots{position:absolute;top:682px;left:554px;display:flex;gap:10px}
  .hero-dots span{width:10px;height:10px;border-radius:50%;background:#fff}
  .hero-dots .active{background:transparent;border:2px solid var(--brand-cyan)}

  /* headings */
  .section-title{font-family:"Orbitron",sans-serif;font-weight:800;color:var(--brand-blue);letter-spacing:1px;line-height:1.15}
  .body-copy{font-size:14px;color:var(--muted);line-height:30.5px}

  /* about */
  .about-mark{position:absolute;left:150px;top:1010px;font-family:"Roboto",sans-serif;font-weight:700;font-size:74px;color:var(--brand-blue)}
  .ghost-word{position:absolute;font-family:"Roboto",sans-serif;font-weight:700;color:rgba(0,0,0,.035);line-height:1}

  /* services */
  .services-title{position:absolute;top:1532px;width:1200px;text-align:center;color:#fff;font-size:40px}
  .services-lede{position:absolute;top:1594px;left:200px;width:800px;text-align:center;color:#fff;font-size:14px;line-height:26px}
  .service{position:absolute;border-radius:50%;background:var(--circle-dark);box-shadow:0 0 0 9px rgba(27,110,170,.55);color:#fff;text-align:center;display:flex;flex-direction:column;align-items:center;justify-content:center}
  .service h3{font-size:19px;font-weight:500;line-height:24px}
  .service p{font-size:11px;line-height:20px;padding:0 22px}
  .service.featured{background:#2a4c97}
  .vertical-word{position:absolute;font-family:"Roboto",sans-serif;font-weight:700;transform-origin:left top;transform:rotate(-90deg);line-height:1;white-space:nowrap}

  /* support */
  .video-frame{position:absolute;left:561px;top:2191px;width:493px;height:340px;background:#fff;padding:5px;box-shadow:0 2px 8px rgba(0,0,0,.15)}
  .video-frame .media{width:100%;height:100%;background:linear-gradient(135deg,#c9ccd4 0%,#e7e3de 45%,#b9a58f 100%)}
  .outline-box{position:absolute;left:907px;top:2143px;width:204px;height:191px;border:3px solid var(--brand-cyan)}

  /* footer */
  .contact-item{position:absolute;top:2760px;width:240px;text-align:center;color:#fff}
  .contact-icon{width:70px;height:70px;border-radius:50%;border:2px solid #fff;margin:0 auto;display:flex;align-items:center;justify-content:center}
  .contact-icon.filled{background:var(--brand-cyan);border-color:var(--brand-cyan)}
  .contact-item h4{margin-top:22px;font-size:15px;font-weight:500}
  .contact-item p{margin-top:6px;font-size:12px;line-height:22px}
  .footer-rule{position:absolute;left:143px;top:2944px;width:911px;height:1px;background:rgba(255,255,255,.35)}
  .legal{position:absolute;left:143px;top:2978px;font-size:13px;color:#fff}
  .socials{position:absolute;left:878px;top:2967px;display:flex;gap:10px}
  .socials span{width:38px;height:38px;border-radius:50%;border:2px solid #fff;color:#fff;font-size:12px;font-weight:700;display:flex;align-items:center;justify-content:center}
</style>
</head>
<body>
<div class="page">

  <svg class="backdrop" width="1200" height="3021" viewBox="0 0 1200 3021" aria-hidden="false">
    <defs>
      <linearGradient id="heroSky" x1="0" y1="0" x2="0" y2="1">
        <stop offset="0" stop-color="#03050a"/>
        <stop offset=".45" stop-color="#0b1628"/>
        <stop offset=".75" stop-color="#2b2a22"/>
        <stop offset="1" stop-color="#101a2b"/>
      </linearGradient>
      <linearGradient id="towerTone" x1="0" y1="0" x2="1" y2="1">
        <stop offset="0" stop-color="#f6f7f9"/>
        <stop offset="1" stop-color="#c9ced6"/>
      </linearGradient>
      <linearGradient id="servicesBand" x1="0" y1="0" x2="0" y2="1">
        <stop offset="0" stop-color="#3d58a8"/>
        <stop offset=".5" stop-color="#2d7fc0"/>
        <stop offset="1" stop-color="#1bb6da"/>
      </linearGradient>
    </defs>

    <g role="img" aria-label="Night view of Earth from orbit with glowing city lights">
      <polygon points="0,107 1200,107 1200,680 0,856" fill="url(#heroSky)"/>
    </g>

    <g role="img" aria-label="Upward view of glass skyscrapers">
      <polygon points="600,760 900,735 960,950 720,930" fill="url(#towerTone)" opacity=".8"/>
      <polygon points="0,860 160,840 260,1390 0,1340" fill="url(#towerTone)" opacity=".7"/>
      <polygon points="1110,1030 1200,1040 1200,1420 1090,1380" fill="url(#towerTone)" opacity=".7"/>
      <polygon points="760,2030 1000,1980 1040,2130 820,2120" fill="url(#towerTone)" opacity=".8"/>
      <polygon points="0,2150 200,2140 330,2650 0,2660" fill="url(#towerTone)" opacity=".7"/>
      <polygon points="1100,2300 1200,2310 1200,2580 1110,2580" fill="url(#towerTone)" opacity=".7"/>
    </g>

    <polygon points="821,733 1200,678 1200,752" fill="#1cb2d6"/>
    <polygon points="1126,762 1200,752 1200,822" fill="#3a55a6"/>

    <polygon points="0,1337 1200,1513 1200,1971 0,2152" fill="url(#servicesBand)"/>

    <polygon points="0,2655 520,2688 0,2700" fill="#3a55a6"/>
    <polygon points="0,2700 470,2700 0,2757" fill="#1cb2d6"/>
    <polygon points="0,2700 1200,2580 1200,3021 0,3021" fill="#1c2a3b"/>
    <polygon points="0,2700 470,2700 0,2757" fill="#1cb2d6"/>
  </svg>

  <header class="site-header">
    <div class="brand"><span class="brand-square"></span><span class="brand-name">Tarvolen</span></div>
    <div class="brand-tag">Tarvolen Border Flow</div>
    <nav class="main-nav">
      <span>HOME</span><span>PRODUCTS</span><span>WEB APP</span><span>ABOUT US</span><span>WORKING AT TARVOLEN</span><span>NEWS</span><span>CONTACT US</span>
    </nav>
    <svg class="nav-search" width="14" height="14" viewBox="0 0 14 14"><circle cx="6" cy="6" r="4.5" fill="none" stroke="#2f4a9e" stroke-width="2"/><line x1="9.3" y1="9.3" x2="13" y2="13" stroke="#2f4a9e" stroke-width="2"/></svg>
  </header>

  <section class="hero">
    <div class="hero-title">Tarvolen</div>
    <div class="hero-tag">Tarvolen Border Flow</div>
    <p class="hero-lede">At vero eos et accusamus et iusto odio dignissimos ducimus<br>qui blanditiis praesentium voluptatum</p>
    <div class="btn" style="left:506px;top:502px;width:188px">GET STARTED <span class="btn-arrow"></span></div>
    <div class="hero-dots"><span></span><span></span><span class="active"></span><span></span><span></span></div>
  </section>

  <section class="about">
    <div class="about-mark">Tarvolen</div>
    <h2 class="section-title abs" style="left:569px;top:912px;font-size:40px">ABOUT US</h2>
    <p class="body-copy abs" style="left:569px;top:981px;width:490px">At vero eos et accusamus et iusto odio dignissimos ducimus qui blanditiis praesentium voluptatum deleniti atque corrupti quos dolores et quas molestias excepturi sint occaecati cupiditate non provident, similique sunt in culpa qui officia deserunt mollitia animi, id est laborum et dolorum fuharum quidem rerum facilis est et expedita distinctio. Nam libero tempore, cum soluta nobis est eligendi optio cumque nihil impedit quo minus id quod maxime placeat facvoluptas assumenda es dolor repellendus.</p>
    <div class="btn" style="left:569px;top:1223px;width:184px">GET STARTED <span class="btn-arrow"></span></div>
    <div class="ghost-word" style="left:795px;top:1310px;font-size:125px">ABOUT</div>
  </section>

  <section class="services">
    <div class="vertical-word" style="left:58px;top:1965px;font-size:82px;color:rgba(255,255,255,.14)">SERVICES</div>
    <h2 class="section-title services-title">WHAT WE DO</h2>
    <p class="services-lede">At vero eos et accusamus et iusto odio dignissimos ducimus qui blanditiis praesentium voluptatum deleniti atque corrupti quos dolores et quas molestias excepturi sint occaecati cupiditate non prculpa qui officia deserunt mollitia animi</p>

    <svg class="abs" style="left:203px;top:1786px" width="34" height="66" viewBox="0 0 34 66"><polyline points="32,1 2,33 32,65" fill="none" stroke="#fff" stroke-width="1.5"/></svg>
    <svg class="abs" style="left:963px;top:1786px" width="34" height="66" viewBox="0 0 34 66"><polyline points="2,1 32,33 2,65" fill="none" stroke="#fff" stroke-width="1.5"/></svg>

    <div class="service" style="left:272px;top:1715px;width:206px;height:206px">
      <svg width="62" height="58" viewBox="0 0 62 58"><circle cx="24" cy="24" r="18" fill="none" stroke="#fff" stroke-width="2"/><circle cx="44" cy="22" r="8" fill="none" stroke="#fff" stroke-width="2"/><circle cx="44" cy="22" r="3" fill="#fff"/><line x1="18" y1="42" x2="18" y2="56" stroke="#fff" stroke-width="2"/></svg>
      <h3 style="margin-top:18px">SAEPE EVEN<br>IETUT</h3>
    </div>
    <div class="service featured" style="left:472px;top:1691px;width:254px;height:254px">
      <h3>NAM LIBERO<br>TEMPORE</h3>
      <p style="margin-top:10px">At vero eos et accusamus et iusto odio dignissimos ducimus qui blanditiis praesentium voluptatum dtque corrupti quos dolores et quamolestias</p>
      <svg style="margin-top:8px" width="14" height="14" viewBox="0 0 14 14"><polyline points="2,2 7,7 12,2" fill="none" stroke="#fff" stroke-width="1.6"/><polyline points="2,7 7,12 12,7" fill="none" stroke="#fff" stroke-width="1.6"/></svg>
    </div>
    <div class="service" style="left:720px;top:1701px;width:206px;height:206px">
      <svg width="52" height="58" viewBox="0 0 52 58"><rect x="12" y="6" width="28" height="20" rx="4" fill="none" stroke="#fff" stroke-width="2"/><circle cx="20" cy="16" r="3" fill="#fff"/><circle cx="32" cy="16" r="3" fill="#fff"/><rect x="8" y="30" width="36" height="24" rx="4" fill="none" stroke="#fff" stroke-width="2"/><line x1="2" y1="36" x2="8" y2="36" stroke="#fff" stroke-width="2"/><line x1="44" y1="36" x2="50" y2="36" stroke="#fff" stroke-width="2"/></svg>
      <h3 style="margin-top:14px">CUM SOLUTA<br>NOBIS</h3>
    </div>
  </section>

  <section class="support">
    <div class="outline-box"></div>
    <div class="vertical-word" style="left:1118px;top:2375px;font-size:72px;color:rgba(47,74,158,.12)">SUPPORT</div>
    <h2 class="section-title abs" style="left:143px;top:2186px;font-size:40px">CUSTOMER<br>SUPPORT</h2>
    <p class="body-copy abs" style="left:143px;top:2296px;width:380px">At vero eos et accusamus et iusto odio dignissimos ducimus qui blanditiispraesentium voluptatum deleniti atque corrupti quos dolores et quas molestias excepturi sint occaecati cupiditate non provident, similique sunt in culpa qui officia quidem rerum facilis est et expedita distinctio.</p>
    <div class="btn" style="left:143px;top:2477px;width:184px">GET STARTED <span class="btn-arrow"></span></div>
    <div class="video-frame">
      <div class="media" role="img" aria-label="Video still of a bright desk with a desktop computer, laptop and lamp"></div>
    </div>
    <svg class="abs" style="left:774px;top:2327px" width="66" height="66" viewBox="0 0 66 66"><circle cx="33" cy="33" r="30" fill="rgba(0,0,0,.15)" stroke="#fff" stroke-width="4"/><polygon points="26,20 48,33 26,46" fill="#fff"/></svg>
  </section>

  <footer class="site-footer">
    <div class="contact-item" style="left:97px">
      <div class="contact-icon"><svg width="24" height="24" viewBox="0 0 24 24"><path d="M5 2 L9 2 L11 7 L8 9 Q10 14 15 16 L17 13 L22 15 L22 19 Q22 22 18 22 Q3 20 2 6 Q2 2 5 2Z" fill="#fff"/></svg></div>
      <h4>PHONE</h4><p>(+410) 555 014 2290</p>
    </div>
    <div class="contact-item" style="left:323px">
      <div class="contact-icon"><svg width="20" height="28" viewBox="0 0 20 28"><path d="M10 1 Q19 1 19 10 Q19 16 10 27 Q1 16 1 10 Q1 1 10 1Z" fill="#fff"/><circle cx="10" cy="10" r="3.5" fill="#1c2a3b"/></svg></div>
      <h4>HEAD OFFICE</h4><p>48 Harlow Quay Road, Brenmoor,<br>Eastvale, USA. PO 7310</p>
    </div>
    <div class="contact-item" style="left:601px">
      <div class="contact-icon filled"><svg width="20" height="28" viewBox="0 0 20 28"><path d="M10 1 Q19 1 19 10 Q19 16 10 27 Q1 16 1 10 Q1 1 10 1Z" fill="#fff"/><circle cx="10" cy="10" r="3.5" fill="#1cb2d6"/></svg></div>
      <h4>MAIN OFFICE</h4><p>48 Harlow Quay Road, Brenmoor,<br>Eastvale, USA. PO 7310</p>
    </div>
    <div class="contact-item" style="left:850px">
      <div class="contact-icon"><svg width="28" height="20" viewBox="0 0 28 20"><rect x="1" y="1" width="26" height="18" rx="2" fill="#fff"/><polyline points="1,2 14,11 27,2" fill="none" stroke="#1c2a3b" stroke-width="2"/></svg></div>
      <h4>EMAIL</h4><p>hello@tarvolen-mail.com</p>
    </div>
    <div class="footer-rule"></div>
    <div class="legal">Copyrights © 2019, Tarvolen. All rights reserved &nbsp;|&nbsp; Privacy Policy &nbsp;|&nbsp; Terms of use</div>
    <div class="socials" aria-label="Social channels"><span>F</span><span>T</span><span>L</span><span>Y</span></div>
  </footer>

</div>
</body>
</html>
```